Employee Benefits and Insurance Consulting

We are an existing company with over 30 years experience but are changing our name. We would like a simple design with grey tones.

Industry/Entity Type

Insurance

Contact Information for Business Card

Marlow Benefits Consulting
Gerald P Hollins CEO
5172 Brackenridge Road
Harlan Creek, TN 37912
gerald@marlowbenefits-example.com
865-412-5593 - O
865-247-3861 - C

```html
<!DOCTYPE html>
<html lang="en">
<head>
<meta charset="utf-8">
<title>Marlow Benefits Consulting – Business Card</title>
<link rel="stylesheet" href="https://fonts.googleapis.com/css2?family=Open+Sans:wght@400;600;700&display=swap">
<style>
  :root {
    --brand-red: #d51317;
    --card-white: #ffffff;
    --rule-light: rgba(255,255,255,0.45);
    --rule-grey: #bdbdbd;
    --page-bg: #ecebe9;
  }
  html, body {
    margin: 0;
    padding: 0;
    width: 1200px;
    height: 900px;
    overflow: hidden;
    background: var(--page-bg);
    font-family: "Open Sans", Arial, sans-serif;
  }
  .canvas {
    position: relative;
    width: 1200px;
    height: 900px;
  }
  .card {
    position: absolute;
    background: var(--card-white);
    box-shadow: 0 6px 18px rgba(0,0,0,0.18);
    overflow: hidden;
  }

  /* Front card */
  .card-front {
    left: 77px;
    top: 34px;
    width: 589px;
    height: 364px;
  }
  .front-accent-bar {
    position: absolute;
    left: 0;
    top: 57px;
    width: 13px;
    height: 251px;
    background: var(--brand-red);
  }
  .brand-block {
    position: absolute;
    left: 13px;
    top: 0;
    width: 283px;
    height: 364px;
    display: flex;
    flex-direction: column;
    align-items: center;
    justify-content: center;
  }
  .brand-name {
    margin: 0;
    color: var(--brand-red);
    font-weight: 700;
    text-align: center;
    line-height: 1.1;
  }
  .brand-block .brand-name { font-size: 30px; }
  .brand-rule {
    width: 250px;
    height: 1px;
    background: var(--rule-grey);
    margin-top: 10px;
  }
  .contact-panel {
    position: absolute;
    left: 296px;
    top: 0;
    width: 293px;
    height: 364px;
    background: var(--brand-red);
    color: var(--card-white);
  }
  .holder-name {
    position: absolute;
    left: 5px;
    top: 34px;
    margin: 0;
    font-size: 20px;
    font-weight: 600;
    white-space: nowrap;
  }
  .holder-title {
    font-size: 15px;
    font-weight: 600;
  }
  .panel-rule {
    position: absolute;
    left: 0;
    width: 293px;
    height: 1px;
    background: var(--rule-light);
  }
  .contact-row {
    position: absolute;
    left: 3px;
    display: flex;
    align-items: center;
    gap: 14px;
    font-size: 15.5px;
    line-height: 1.3;
    white-space: nowrap;
  }
  .contact-icon {
    width: 32px;
    height: 32px;
    flex: none;
  }
  .contact-email {
    font-size: 13px;
    letter-spacing: -0.1px;
  }
  .contact-row-email { gap: 11px; }

  /* Back card */
  .card-back {
    left: 388px;
    top: 505px;
    width: 567px;
    height: 352px;
  }
  .back-brand {
    position: absolute;
    left: 0;
    top: 0;
    width: 567px;
    height: 330px;
    display: flex;
    flex-direction: column;
    align-items: center;
    justify-content: center;
  }
  .back-brand .brand-name { font-size: 38px; }
  .back-brand .brand-rule { width: 290px; }
  .back-footer {
    position: absolute;
    left: 0;
    bottom: 0;
    width: 567px;
    height: 44px;
  }
</style>
</head>
<body>
<main class="canvas">

  <section class="card card-front" aria-label="Business card front">
    <div class="front-accent-bar"></div>

    <div class="brand-block">
      <p class="brand-name">Marlow Benefits<br>Consulting</p>
      <div class="brand-rule"></div>
    </div>

    <div class="contact-panel">
      <p class="holder-name">Gerald P Hollins - <span class="holder-title">CEO</span></p>
      <div class="panel-rule" style="top:73px"></div>
      <div class="panel-rule" style="top:156px"></div>

      <div class="contact-row" style="top:163px">
        <svg class="contact-icon" viewBox="0 0 32 32" aria-hidden="true">
          <circle cx="16" cy="16" r="16" fill="#fff"/>
          <path d="M16 7a6 6 0 0 0-6 6c0 4.5 6 12 6 12s6-7.5 6-12a6 6 0 0 0-6-6z" fill="var(--brand-red)"/>
          <circle cx="16" cy="13" r="2.3" fill="#fff"/>
        </svg>
        <span>5172 Brackenridge Road<br>Harlan Creek, TN 37912</span>
      </div>
      <div class="panel-rule" style="top:211px"></div>

      <div class="contact-row" style="top:217px">
        <svg class="contact-icon" viewBox="0 0 32 32" aria-hidden="true">
          <circle cx="16" cy="16" r="16" fill="#fff"/>
          <path d="M11.5 8.5l3 3-1.8 2a11 11 0 0 0 5.8 5.8l2-1.8 3 3-2 2.5c-6 0-13-7-13-13z" fill="var(--brand-red)"/>
        </svg>
        <span>865-247-3861</span>
      </div>
      <div class="panel-rule" style="top:253px"></div>

      <div class="contact-row" style="top:259px">
        <svg class="contact-icon" viewBox="0 0 32 32" aria-hidden="true">
          <circle cx="16" cy="16" r="16" fill="#fff"/>
          <rect x="11" y="7" width="10" height="18" rx="1.5" fill="var(--brand-red)"/>
          <rect x="12.5" y="9.5" width="7" height="11" fill="#fff"/>
          <circle cx="16" cy="22.7" r="1" fill="#fff"/>
        </svg>
        <span>865-412-5593</span>
      </div>
      <div class="panel-rule" style="top:294px"></div>

      <div class="contact-row contact-row-email" style="top:300px">
        <svg class="contact-icon" viewBox="0 0 32 32" aria-hidden="true">
          <circle cx="16" cy="16" r="16" fill="#fff"/>
          <rect x="8" y="10" width="16" height="12" fill="var(--brand-red)"/>
          <path d="M8.5 10.5L16 17l7.5-6.5" fill="none" stroke="#fff" stroke-width="1.4"/>
        </svg>
        <span class="contact-email">gerald@marlowbenefits-example.com</span>
      </div>
      <div class="panel-rule" style="top:333px"></div>
    </div>
  </section>

  <section class="card card-back" aria-label="Business card back">
    <div class="back-brand">
      <p class="brand-name">Marlow Benefits<br>Consulting</p>
      <div class="brand-rule"></div>
    </div>
    <svg class="back-footer" viewBox="0 0 567 44" aria-hidden="true">
      <polygon points="0,22 267,22 284,6 301,22 567,22 567,44 0,44" fill="var(--brand-red)"/>
    </svg>
  </section>

</main>
</body>
</html>
```